Plimsy Salve by Tiny Wrens: All Natural Lip Balm Co. Looking for New Label

Greetings, our company is called Tiny Wrens and we are a start-up founded in early 2014. We make 100% All-Natural lip balm, called Plimsy Salve, in a variety of flavors and we are looking for a new label that incorporates part of our logo and highlights our product name and our lip balms flavor (see attached files). Our website is: plimsysalve.example, and we are on Twitter: @TinyWrensSalves, and Facebook: /TinyWrensSalves. Our lip balms are made with beeswax, sweet almond oil, shea butter, coconut oil and other all natural oils and flavors.

The design should be clean, and communicate comfort, its "all-natural-ness", reliability, and fun. The colors we would like to have incorporated are burgundy, a deep, but not dark orange (see files, website, logo, graphics), some green and maybe gold/yellow. Given that the lip balm tubes are small (standard tubes), we would like to assure that the lip balm name, the flavor, and part of the logo- (perhaps the bee), are clearly visible and easily read. I am open to a variety of fonts, as long as they convey what I have stated above.

We want to use the label graphics and our logo for not only labeling our product, but also for use on our website, on banners, signs, retail boxes, letterhead, tee shirts, etc. If we like the design we are open to working with you again as our company is growing and we will be expanding our product line within the year to include hand and body balms, as well as other similar items and we will eventually have a few different product lines marketed at various age groups as well. Our lip balm is currently marketed to 14 to 40+ demographic, with the average age being roughly in the 15 to 24 range and our lip balm has been purchased by more women than men, though we market to both.

As far as software goes, I would like it to be in a format that is most popular- my old logo and graphics were made in Adobe Creative Suite 5.0, Adobe InDesign, and Adobe Illustrator, so the label should be made using this software (or a higher version). If I can have the label in a JPEG format also so I personally can add it to my website and social media that would be great.

I have a label redesign doc in an indd format but it was too large to upload. I believe this was the entire layout of our last label. If you need this, or anything else, please let me know as well as how I can send it to you.

We have applied to the popular TV show Otter Pond and recently received a call back with interest from the producers; we are so excited and hope you are as well!

Thank you!
Todd Vaselko
Owner
Tiny Wrens Salves LLC
Todd@TinyWrensSalves.example

The Label dimensions are: 2.25 inches wide ---> by 2 inches long. Currently, there is a .75 inch area that is part of the label and is perforated, used as a safety seal. I may be changing the labels to a slightly different kind but the dimensions will be the same. The tubes we use are standard lip balm tubes with a net weight of .15 ounces ( the total length of the tube from the bottom turning piece to the top of the cap is just over 2.5 inches (this is NOT how large the label must be).We are discontinuing the 1 Hive, 2 Hive concepts ( for different consistencies of the balm) so that part of the label does not need to be included.Feel free to enhance and/or modify the logo to fit the design of the label.Thank you! Added Thursday, February 12, 2015

Industry/Entity Type

Software

Requirements
Must have
• Label Dimensions:
• Length: 2.125" Height: 2.125"
• Top Margin: 1.025" Bottom Margin: 1.025"
• Left Margin: 0.9125" Right Margin: 0.9125"
• Horizontal Spacing: 0.15" Vertical Spacing: 0.15"
• Horizontal Pitch: 2.275" Vertical Pitch: 2.275"

```html
<!DOCTYPE html>
<html lang="en">
<head>
<meta charset="utf-8">
<title>Plimsy Salve – Lip Balm Label</title>
<link href="https://fonts.googleapis.com/css2?family=Antonio:wght@400;500&family=Arimo:wght@700&display=swap" rel="stylesheet">
<style>
  :root {
    --backdrop: #ececec;
    --label-white: #ffffff;
    --comb-cream: #fdf6ea;
    --honey: #eaa522;
    --honey-deep: #d9901a;
    --honey-soft: #f6d9a0;
    --ink-white: #ffffff;
  }
  * { margin: 0; padding: 0; box-sizing: border-box; }
  html, body {
    width: 1200px; height: 1200px; overflow: hidden;
    background: var(--backdrop);
  }
  .label {
    position: absolute; left: 390px; top: 120px;
    width: 420px; height: 960px;
    background: var(--label-white);
    box-shadow: 0 4px 18px rgba(0,0,0,0.08);
    overflow: hidden;
  }
  .name-band {
    position: relative; z-index: 1;
    height: 110px; background: var(--honey);
    display: flex; align-items: center; white-space: nowrap;
    overflow: hidden;
  }
  .name-band span {
    font-family: "Antonio", sans-serif; font-weight: 500;
    font-size: 78px; color: var(--ink-white);
    letter-spacing: -1px; margin-left: -40px; margin-right: 60px;
  }
  .comb-field {
    position: absolute; left: 0; top: 110px; right: 0; bottom: 0;
    background: linear-gradient(180deg, var(--label-white), var(--comb-cream));
  }
  .maker-mark {
    position: absolute; left: 0; right: 0; top: 210px;
    display: flex; align-items: center; justify-content: center; gap: 12px;
  }
  .maker-mark .dot {
    width: 34px; height: 34px; border-radius: 50%; background: var(--honey);
  }
  .maker-mark .maker-name {
    font-family: "Arimo", sans-serif; font-weight: 700;
    font-size: 34px; color: var(--honey-deep);
  }
  .drop-ornament {
    position: absolute; left: 160px; top: 330px;
    width: 100px; height: 150px; border-radius: 50% 50% 48% 48%;
    background: radial-gradient(circle at 50% 60%, var(--honey-soft), var(--honey));
  }
  .product-title {
    position: absolute; left: 10px; right: 10px; top: 535px;
    text-align: center;
    font-family: "Antonio", sans-serif; font-weight: 500;
    font-size: 90px; line-height: 1; color: var(--honey);
    letter-spacing: -2px; white-space: nowrap;
  }
  .product-type {
    position: absolute; left: 18px; right: 18px; top: 670px;
    border-top: 2px solid var(--honey); border-bottom: 2px solid var(--honey);
    padding: 8px 0 6px;
    text-align: center;
    font-family: "Arimo", sans-serif; font-weight: 700;
    font-size: 33px; color: var(--honey); letter-spacing: 0.5px;
  }
  .flavor-pill {
    position: absolute; left: 20px; right: 20px; top: 760px;
    height: 64px; border-radius: 32px; background: var(--honey);
    display: flex; align-items: center; justify-content: center;
    font-family: "Arimo", sans-serif; font-weight: 700;
    font-size: 30px; color: var(--ink-white);
  }
</style>
</head>
<body>
  <main class="label">
    <div class="name-band">
      <span>Plimsy Salve</span><span>Plimsy Salve</span>
    </div>
    <div class="comb-field" role="img" aria-label="Faint honeycomb pattern background"></div>
    <div class="maker-mark">
      <span class="dot"></span>
      <span class="maker-name">Tiny Wrens</span>
    </div>
    <div class="drop-ornament" role="img" aria-label="Honey drop with leaf ornament"></div>
    <h1 class="product-title">Plimsy Salve</h1>
    <p class="product-type">BEESWAX LIP BALM</p>
    <p class="flavor-pill">Brown Sugar Cookie</p>
  </main>
</body>
</html>
```